Harborview Estates Business Card for Apartment Buildings

Create business cards for resident managers who run apartment buildings. The audience is the public who are searching for apartment rentals, and current residents who live at the apartment building. Key design element will be incorporating the company logo, however, the logo cannot dominate. The building name and manager name are more important than the logo. Current business card design leaves little room for copy, so we may need to reduce the size on the current card to allow for more space for copy.

Target Market(s)

Adults 18-65 years of age, who are looking for an apartment rental, plus current residents who live at our apartment buildings.

Industry/Entity Type

Property Management

Contact Information for Business Card

A major design element will be use of the company logo. Important property and manager contact information must be part of the design. The size of the logo will need to be reduced to make room for building and manager contact copy.

Font styles to use
Sans Serif

Colors
3176b5
000000
959595
ffffff

Requirements
Must have
• 1) Incorporate the company logo.
• 2) Use the company colors (dark blue, black/grey, over white).
• 3) FEATURE THE BUILDING NAME
• 4) FEATURE THE MANAGER NAME
• 5) The company name is less important than BUILDING and MANAGER
• 6) Manager contact information
• **SEE ATTACHED CREATIVE BRIEF**
Nice to have
• 1) Back of card logo watermark
• 2) Ability to write notes on back of carfd
Should not have
• Avoid letting the company logo dominate the card, the building name and manager are more important than the company logo.

```html
<!DOCTYPE html>
<html lang="en">
<head>
<meta charset="utf-8">
<title>Harborview Estates Business Card</title>
<link href="https://fonts.googleapis.com/css2?family=Montserrat:wght@400;600;700&display=swap" rel="stylesheet">
<style>
  :root {
    --blue-light: #2f9ad8;
    --blue: #3176b5;
    --blue-deep: #1f64a3;
    --grey: #959595;
    --grey-light: #e9ecef;
    --white: #ffffff;
    --black: #000000;
    --page: #eef1f4;
  }
  * { margin: 0; padding: 0; box-sizing: border-box; }
  html, body {
    width: 1200px; height: 900px; overflow: hidden;
    background: var(--page);
    font-family: "Montserrat", sans-serif;
  }
  .card {
    position: absolute;
    left: 285px;
    width: 630px; height: 360px;
    border-radius: 18px;
    overflow: hidden;
    box-shadow: 0 10px 28px rgba(0,0,0,.18);
  }

  /* Company side */
  .card-company-side {
    top: 50px;
    background: linear-gradient(135deg, var(--blue-light) 0%, var(--blue) 60%, var(--blue-deep) 100%);
  }
  .company-side-ring {
    position: absolute; left: 235px; top: 40px;
    width: 280px; height: 280px; border-radius: 50%;
    background: rgba(255,255,255,.06);
  }
  .company-lockup {
    position: absolute; left: 0; right: 0; top: 132px;
    display: flex; align-items: center; justify-content: center; gap: 12px;
    color: var(--white); font-weight: 700; text-transform: uppercase;
  }
  .company-mark { width: 30px; height: 30px; background: var(--white); flex: none; }
  .company-words { display: flex; flex-direction: column; line-height: 1.05; }
  .company-line-1 { font-size: 30px; letter-spacing: 1px; }
  .company-line-2 { font-size: 14px; letter-spacing: 4px; margin-top: 3px; }
  .website {
    position: absolute; left: 0; right: 0; bottom: 46px; text-align: center;
    color: var(--white); font-size: 14px; font-weight: 600; letter-spacing: 1.5px;
  }

  /* Contact side */
  .card-contact-side {
    top: 490px;
    background: linear-gradient(135deg, var(--blue-light) 0%, var(--blue) 70%, var(--blue-deep) 100%);
  }
  .feature-circle {
    position: absolute; left: 300px; top: -150px;
    width: 440px; height: 440px; border-radius: 50%;
    background: linear-gradient(160deg, var(--white) 30%, var(--grey-light) 100%);
    border: 16px solid var(--grey);
  }
  .contact-company {
    position: absolute; left: 392px; top: 76px;
    display: flex; align-items: center; gap: 8px;
    color: var(--blue); font-weight: 700; font-size: 15px; letter-spacing: .5px;
    text-transform: uppercase; white-space: nowrap;
  }
  .contact-company .company-mark { width: 16px; height: 16px; background: var(--blue); }
  .contact-block {
    position: absolute; left: 40px; top: 62px; color: var(--white);
  }
  .manager-name { font-size: 24px; font-weight: 700; }
  .manager-title { font-size: 13px; font-weight: 400; margin-top: 3px; }
  .divider { width: 52px; height: 2px; background: var(--white); margin: 12px 0; }
  .address { font-size: 13px; line-height: 1.45; margin-bottom: 10px; }
  .contact-list { list-style: none; font-size: 13px; }
  .contact-list li { display: flex; align-items: center; gap: 9px; height: 20px; }
  .contact-list svg { width: 13px; height: 13px; fill: var(--white); flex: none; }
  .building-name {
    position: absolute; left: 40px; bottom: 26px;
    color: var(--white); font-size: 17px; font-weight: 700; letter-spacing: 1.5px;
    text-transform: uppercase;
  }
</style>
</head>
<body>

<section class="card card-company-side">
  <div class="company-side-ring"></div>
  <div class="company-lockup">
    <span class="company-mark"></span>
    <span class="company-words">
      <span class="company-line-1">Harborview</span>
      <span class="company-line-2">Estates LLC</span>
    </span>
  </div>
  <p class="website">www.harborviewestates.com</p>
</section>

<section class="card card-contact-side">
  <div class="feature-circle"></div>
  <div class="contact-company">
    <span class="company-mark"></span>
    <span>Harborview Estates</span>
  </div>

  <div class="contact-block">
    <h1 class="manager-name">Marisol Vega</h1>
    <p class="manager-title">Resident Manager</p>
    <div class="divider"></div>
    <p class="address">1480 Cedar Lane<br>Bayport CA 90412</p>
    <ul class="contact-list">
      <li>
        <svg viewBox="0 0 16 16" aria-hidden="true"><path d="M3.6 1.2l2.3 2.6-1.3 1.8c.9 2 2.4 3.5 4.4 4.4l1.8-1.3 2.6 2.3-1.4 2.5C6.6 14.8 1.2 9.4 1.1 2.6z"/></svg>
        555-201-4410
      </li>
      <li>
        <svg viewBox="0 0 16 16" aria-hidden="true"><path d="M4 1h8v4H4zM1 6h14v6h-3v3H4v-3H1zm4 4v4h6v-4z"/></svg>
        555-201-4412
      </li>
      <li>
        <svg viewBox="0 0 16 16" aria-hidden="true"><path d="M4 0h8a1 1 0 011 1v14a1 1 0 01-1 1H4a1 1 0 01-1-1V1a1 1 0 011-1zm1 2v10h6V2zm3 11a1 1 0 100 2 1 1 0 000-2z"/></svg>
        555-201-4415
      </li>
      <li>
        <svg viewBox="0 0 16 16" aria-hidden="true"><path d="M1 3h14v10H1zm1.5 1.5v.3L8 9l5.5-4.2v-.3zm0 2.2v4.8h11V6.7L8 11z"/></svg>
        marisol@harborviewest.com
      </li>
    </ul>
  </div>

  <p class="building-name">Bayside Court Apartments</p>
</section>

</body>
</html>
```